Maris Dovey Studio Business Cards

Hi - using the information and logo provided I require a two sided business card designed with the following information. The business card is a 'mini card' 3.5" x 1.25".

Front of card should be the logo attached but inverted (so the background is the peach colour and the logo white).

Back should have these details. If we can't fit the Pictogrum and Friendwall part can we just put the little logos.

Tessa Varnold

Art and Design Consultant
Dealer - Curator - Events - Styling - Creative Sourcing

P: 0438 217 604
E: tessa@marisdoveystudio.example
W: www.marisdoveystudio.example
I (pictogram image please): marisdoveystudio F (Friendwall image please): MarisDoveyAdviser

Target Market(s)

Galleries, artists, art buyers, interior design clients, event managers, creative types

Industry/Entity Type

Business

```html
<!DOCTYPE html>
<html lang="en">
<head>
<meta charset="utf-8">
<title>Maris Dovey Studio – Mini Business Cards</title>
<link rel="stylesheet" href="https://fonts.googleapis.com/css2?family=Lora:wght@400&family=Open+Sans:wght@400&display=swap">
<style>
  :root {
    --backdrop: #8e8e8e;
    --peach: #f4bc9f;
    --paper: #ffffff;
    --ink: #2f2f2f;
    --ink-soft: #555555;
    --icon: #f4bc9f;
  }
  * { box-sizing: border-box; margin: 0; padding: 0; }
  html, body {
    width: 1200px;
    height: 988px;
    overflow: hidden;
    background: var(--backdrop);
  }
  .canvas {
    position: relative;
    width: 1200px;
    height: 988px;
  }
  .card {
    position: absolute;
    left: 86px;
    width: 1028px;
    height: 366px;
  }
  .card--front {
    top: 102px;
    background: var(--peach);
  }
  .card--back {
    top: 537px;
    height: 368px;
    background: var(--paper);
  }

  /* Front: brand block */
  .front-brand {
    position: absolute;
    left: 0;
    right: 0;
    top: 76px;
    display: flex;
    flex-direction: column;
    align-items: center;
  }
  .front-brand__dot {
    width: 104px;
    height: 104px;
    border-radius: 50%;
    background: var(--paper);
  }
  .front-brand__name {
    margin-top: 58px;
    font-family: "Lora", Georgia, serif;
    font-weight: 400;
    font-size: 38px;
    letter-spacing: 6px;
    text-transform: uppercase;
    color: var(--paper);
  }

  /* Back: contact details */
  .holder-name {
    position: absolute;
    left: 44px;
    top: 46px;
    font-family: "Lora", Georgia, serif;
    font-weight: 400;
    font-size: 46px;
    color: var(--peach);
  }
  .holder-role,
  .holder-services {
    position: absolute;
    left: 44px;
    font-family: "Open Sans", Arial, sans-serif;
    font-size: 24px;
    color: var(--ink);
  }
  .holder-role { top: 116px; }
  .holder-services { top: 162px; }

  .social {
    position: absolute;
    left: 44px;
    top: 242px;
    list-style: none;
    font-family: "Open Sans", Arial, sans-serif;
    font-size: 24px;
    color: var(--ink-soft);
  }
  .social__item {
    display: flex;
    align-items: center;
    height: 46px;
  }
  .social__mark {
    width: 30px;
    height: 30px;
    background: var(--icon);
    margin-right: 18px;
  }

  .contact {
    position: absolute;
    right: 50px;
    top: 218px;
    list-style: none;
    text-align: right;
    font-family: "Open Sans", Arial, sans-serif;
    font-size: 24px;
    color: var(--ink-soft);
  }
  .contact__item {
    height: 44px;
    line-height: 44px;
  }

  .back-brand {
    position: absolute;
    right: 18px;
    top: 40px;
    width: 240px;
    display: flex;
    flex-direction: column;
    align-items: center;
  }
  .back-brand__dot {
    width: 88px;
    height: 88px;
    border-radius: 50%;
    background: var(--peach);
  }
  .back-brand__name {
    margin-top: 14px;
    font-family: "Lora", Georgia, serif;
    font-weight: 400;
    font-size: 15px;
    letter-spacing: 2px;
    text-transform: uppercase;
    color: var(--peach);
  }
</style>
</head>
<body>
<main class="canvas">

  <section class="card card--front" aria-label="Card front">
    <div class="front-brand">
      <div class="front-brand__dot"></div>
      <p class="front-brand__name">Maris Dovey Studio</p>
    </div>
  </section>

  <section class="card card--back" aria-label="Card back">
    <h1 class="holder-name">Tessa Varnold</h1>
    <p class="holder-role">Art and Design Consultant</p>
    <p class="holder-services">Dealer - Curator - Events - Styling - Creative Sourcing</p>

    <ul class="social">
      <li class="social__item"><span class="social__mark" role="img" aria-label="Pictogrum"></span>marisdoveystudio</li>
      <li class="social__item"><span class="social__mark" role="img" aria-label="Friendwall"></span>MarisDoveyAdviser</li>
    </ul>

    <ul class="contact">
      <li class="contact__item">0438 217 604</li>
      <li class="contact__item">tessa@marisdoveystudio.example</li>
      <li class="contact__item">www.marisdoveystudio.example</li>
    </ul>

    <div class="back-brand">
      <div class="back-brand__dot"></div>
      <p class="back-brand__name">Maris Dovey Studio</p>
    </div>
  </section>

</main>
</body>
</html>
```